Modern Business Card

Modern professional business card with more than just logo and demographic info. Something memorable.

We are a trendy/modern chiropractic group with an emphasis on neurology, hence the minimalist-type brain logo. We want to convey that modern and technical aspect with professionalism and the elite nature of our practice environment.

```html
<!DOCTYPE html>
<html lang="en">
<head>
<meta charset="utf-8">
<title>Cadence Chiropractic – Business Card</title>
<link href="https://fonts.googleapis.com/css2?family=Lato:wght@300;400;700&display=swap" rel="stylesheet">
<style>
  :root {
    --stage: #d9d9d9;
    --card: #ffffff;
    --brand-blue: #4682c6;
    --ink: #1a1a1a;
    --ink-soft: #444444;
    --rule: #333333;
  }
  * { box-sizing: border-box; margin: 0; padding: 0; }
  html, body { width: 1200px; height: 801px; overflow: hidden; }
  body {
    background: var(--stage);
    font-family: "Lato", Arial, sans-serif;
    color: var(--ink);
    position: relative;
  }
  .card {
    position: absolute;
    top: 246px;
    width: 540px;
    height: 309px;
    background: var(--card);
    box-shadow: 0 6px 18px rgba(0,0,0,0.12);
    overflow: hidden;
  }
  .card--contact { left: 40px; }
  .card--brand { left: 620px; }

  .band {
    position: absolute;
    left: 0; right: 0;
    bottom: 18px;
    height: 26px;
    background: var(--brand-blue);
    color: #fff;
    font-size: 13px;
    font-weight: 400;
    line-height: 26px;
    letter-spacing: 0.2px;
    padding: 0 26px;
  }
  .card--contact .band { text-align: right; }
  .card--brand .band { text-align: right; font-size: 15px; }

  /* Wordmark */
  .wordmark {
    position: absolute;
    display: flex;
    align-items: center;
    gap: 10px;
  }
  .wordmark__square {
    background: var(--brand-blue);
    flex: none;
  }
  .wordmark__name {
    font-weight: 700;
    color: var(--ink);
    line-height: 1.05;
    letter-spacing: 1px;
  }
  .card--contact .wordmark { left: 56px; top: 108px; }
  .card--contact .wordmark__square { width: 30px; height: 30px; }
  .card--contact .wordmark__name { font-size: 15px; }

  .card--brand .wordmark { left: 118px; top: 104px; gap: 16px; }
  .card--brand .wordmark__square { width: 56px; height: 56px; }
  .card--brand .wordmark__name { font-size: 26px; letter-spacing: 1.5px; }

  /* Person */
  .person {
    position: absolute;
    left: 270px;
    top: 52px;
    padding-left: 10px;
    border-left: 1px solid var(--rule);
  }
  .person__name {
    font-size: 15px;
    letter-spacing: 0.3px;
  }
  .person__name strong { font-weight: 700; }
  .person__name span { font-weight: 300; }
  .person__role {
    font-size: 10px;
    font-weight: 400;
    color: var(--ink-soft);
    margin-top: 2px;
  }

  .contacts {
    position: absolute;
    left: 290px;
    top: 118px;
    padding-left: 10px;
    border-left: 1px solid var(--rule);
    list-style: none;
  }
  .contacts li {
    display: flex;
    align-items: center;
    gap: 8px;
    font-size: 10.5px;
    color: var(--ink);
    height: 17px;
  }
  .contacts svg { width: 11px; height: 11px; flex: none; }
</style>
</head>
<body>

  <section class="card card--contact" aria-label="Card front with contact details">
    <div class="wordmark">
      <span class="wordmark__square"></span>
      <span class="wordmark__name">CADENCE<br>CHIROPRACTIC</span>
    </div>

    <div class="person">
      <p class="person__name"><strong>DR. OWEN</strong> <span>TALLEY</span></p>
      <p class="person__role">Chiropractic</p>
    </div>

    <ul class="contacts">
      <li>
        <svg viewBox="0 0 12 12" aria-hidden="true"><rect width="12" height="12" rx="2" fill="#4682c6"/><path d="M3.3 2.6 4.6 2.4 5.3 4 4.5 4.6c.4.9 1.1 1.6 2 2l.6-.8 1.6.7-.2 1.3C6 7.9 3.3 5.2 3.3 2.6z" fill="#fff"/></svg>
        (555) 014-2270
      </li>
      <li>
        <svg viewBox="0 0 12 12" aria-hidden="true"><rect width="12" height="12" rx="2" fill="#4682c6"/><rect x="2.5" y="3.5" width="7" height="5" fill="none" stroke="#fff" stroke-width="0.9"/><path d="M2.5 3.5 6 6.3 9.5 3.5" fill="none" stroke="#fff" stroke-width="0.9"/></svg>
        owen@cadencechiro.com
      </li>
      <li>
        <svg viewBox="0 0 12 12" aria-hidden="true"><rect width="12" height="12" rx="2" fill="#555"/><circle cx="6" cy="6" r="3.4" fill="none" stroke="#fff" stroke-width="0.8"/><path d="M2.6 6h6.8M6 2.6c-1.6 2-1.6 4.8 0 6.8M6 2.6c1.6 2 1.6 4.8 0 6.8" fill="none" stroke="#fff" stroke-width="0.7"/></svg>
        www.cadencechiro.com
      </li>
    </ul>

    <div class="band">2750 Linden Park Rd, Fairview, OH 43000, United States</div>
  </section>

  <section class="card card--brand" aria-label="Card back with practice name">
    <div class="wordmark">
      <span class="wordmark__square"></span>
      <span class="wordmark__name">CADENCE<br>CHIROPRACTIC</span>
    </div>
    <div class="band">www.cadencechiro.com</div>
  </section>

</body>
</html>
```